CREATE A KILLER WEBSITE DESIGN

We are a firearms training company that trains CIVILIANS (no police or military pictures - thank you!) to defend themselves and are looking for a killer design that's clean, easy to navigate and modern! We want the newest trends applied to this sight like a scrollable site so you can scroll down and see all the features. We are okay with tweaking the HTML but need the artistic design to look good. I'll provide a link to our current site along with a sight we really like so you can get an idea!

I'm supplying a PowerPoint Design we are going with from another designer so you can match the style to the new site.

PAGES: (Please use information from our current site. We like the information but just want a more polished look similar to the NWDPA site below but in our colors.)
Home - Long Form Scrolling Site. Top fold will be a video with a play button.
Harbor Institute - Seven Level Training Program Info Page That Will Contain A Video.
Contact Us - This will be a page that DOES NOT CONTAIN AN EMAIL ADDRESS. Just a contact us form
Meet The Trainer: Dennis Pollock

Our site:
https://www.brightmeadowskills.biz

Sights We Like:
https://www.nwdefenseplanners.com
https://quorvel.com
https://lindenplatecorp.com
https://www.velbrookgear.com

Target Market(s)

Men and women ages 21 to 100 years old

Industry/Entity Type

Self Defense

Number of Pages Required

5+ page

Font styles to use
Sans Serif

Colors
f26267

Requirements
Must have
• Clean and engaging. Use of colors that match our logo.
Should not have
• Poor design quality

```html
<!DOCTYPE html>
<html lang="en">
<head>
<meta charset="utf-8">
<title>Bright Meadow Skills – Concealed Carry Training</title>
<link rel="stylesheet" href="https://fonts.googleapis.com/css2?family=Bebas+Neue&family=Raleway:ital,wght@0,400;0,500;0,600;0,700;1,400&family=Orbitron:wght@600&display=swap">
<style>
:root{
  --red:#e3162b;
  --black:#050505;
  --ink:#0d0d0d;
  --white:#ffffff;
  --grey:#bfbfbf;
  --star:#f5a623;
}
*{margin:0;padding:0;box-sizing:border-box}
html,body{width:1200px;height:4468px;overflow:hidden;background:var(--black)}
body{position:relative;font-family:'Raleway',sans-serif;color:var(--white)}
.abs{position:absolute}
.display{font-family:'Bebas Neue',sans-serif;letter-spacing:.5px}
.btn{position:absolute;display:flex;align-items:center;justify-content:center;font-family:'Raleway',sans-serif;font-weight:700;font-size:16px;text-transform:uppercase;color:var(--white);background:var(--red)}
.btn--dark{background:var(--black)}

/* header */
.site-header{left:0;top:0;width:1200px;height:114px;background:var(--black)}
.brand{display:flex;align-items:center;gap:10px;font-family:'Raleway',sans-serif;font-weight:700;font-size:17px;color:var(--white);text-transform:uppercase;letter-spacing:.5px}
.brand__dot{width:26px;height:26px;border-radius:50%;background:var(--red)}
.main-nav{left:320px;top:77px;display:flex;gap:38px;font-size:14px;font-weight:500}
.main-nav .is-active{color:var(--red)}
.login{left:758px;top:24px;display:flex;align-items:center;gap:8px;font-size:15px;font-weight:500}
.login__icon{width:28px;height:28px;border:2px solid var(--white);border-radius:50%}

/* hero */
.hero{left:0;top:114px;width:1200px;height:686px;clip-path:polygon(0 0,100% 0,100% 571px,50% 684px,0 571px);
  background:linear-gradient(180deg,#6f7670 0%,#8d8f86 30%,#5e7a47 55%,#4d6b37 80%,#3f5a2e 100%)}
.play{position:absolute;border-radius:50%;background:rgba(0,0,0,.85);display:flex;align-items:center;justify-content:center}
.play::after{content:"";border-left:20px solid var(--white);border-top:12px solid transparent;border-bottom:12px solid transparent;margin-left:5px}
.hero__quote{left:0;top:500px;width:1200px;text-align:center;font-size:39px;line-height:45px;text-shadow:0 2px 6px rgba(0,0,0,.6)}
.scroll-cue{left:591px;top:724px;width:18px;height:28px;border:2px solid #9a9a9a;border-radius:9px}

/* about */
.instructor-photo{left:206px;top:985px;width:278px;height:278px;border-radius:50%;background:radial-gradient(circle at 50% 40%,#9a9a9a,#3a3a3a);border:6px solid #111}
.eyebrow{left:642px;top:885px;font-size:16px;font-weight:500;color:var(--red);text-transform:uppercase}
.instructor-name{left:640px;top:912px;font-size:66px;line-height:66px}
.about-copy{left:642px;top:992px;width:442px;font-size:13.2px;line-height:26.5px}

/* levels */
.levels-bg{left:0;top:1338px;width:1200px;height:1390px;background:radial-gradient(ellipse at 50% 30%,#262626 0%,#121212 45%,#070707 100%)}
.levels-title{left:0;top:1496px;width:1200px;text-align:center;font-size:40px}
.red{color:var(--red)}
.levels-copy{left:150px;top:1554px;width:900px;text-align:center;font-size:12.4px;line-height:26.5px}
.level{position:absolute;width:232px;height:165px;border:2px solid #d9d9d9;background:rgba(0,0,0,.55);display:flex;flex-direction:column;align-items:center;justify-content:center;text-align:center}
.level__num{font-family:'Orbitron',sans-serif;font-weight:600;font-size:30px;color:var(--red);letter-spacing:3px;margin-bottom:8px}
.level__name{font-size:19px;line-height:25px;font-weight:500}
.promo-video{left:146px;top:2160px;width:908px;height:445px;background:linear-gradient(160deg,#c81a14 0%,#9c1410 40%,#2b2b2b 75%,#141414 100%)}

/* stories */
.stories-bg{left:0;top:2728px;width:1200px;height:720px;background:radial-gradient(ellipse at 50% 20%,#2a2a2a 0%,#101010 55%,#060606 100%)}
.stories-title{left:0;top:2860px;width:1200px;text-align:center;font-size:50px}
.story{position:absolute;top:2989px;width:310px;height:299px;border:2px solid #cfcfcf;background:rgba(0,0,0,.6);padding:58px 40px 0}
.story__avatar{position:absolute;top:-46px;left:111px;width:88px;height:88px;border-radius:50%;border:3px solid var(--red);background:radial-gradient(circle at 50% 40%,#d8d8d8,#7b7b7b)}
.story__who{display:flex;align-items:center;gap:10px;font-size:14px;text-transform:uppercase;font-weight:500}
.story__mark{font-family:'Bebas Neue',sans-serif;font-size:54px;line-height:30px;height:30px}
.story__text{margin-top:18px;font-style:italic;font-size:11.6px;line-height:22px}
.story__stars{position:absolute;left:40px;top:266px;color:var(--star);font-size:15px;letter-spacing:2px}
.dots{left:556px;top:3332px;display:flex;align-items:center;gap:12px}
.dots i{width:6px;height:6px;border-radius:50%;background:var(--white)}
.dots i.on{width:12px;height:12px}

/* contact */
.contact-bg{left:0;top:3448px;width:1200px;height:720px;background:linear-gradient(180deg,#0e0e0e,#131313)}
.contact-title{left:0;top:3485px;width:1200px;text-align:center;font-size:44px}
.field{position:absolute;border:2px solid #4a4a4a;background:transparent;font-size:13px;color:#a8a8a8;padding:0 16px;display:flex;align-items:center;gap:8px}
.field--area{align-items:flex-start;padding-top:14px}

/* footer */
.footer-nav{left:0;top:4312px;width:1200px;display:flex;justify-content:center;gap:40px;font-size:16px;font-weight:500}
.social{position:absolute;top:4364px;width:32px;height:32px;border-radius:50%;background:var(--white)}
.copyright{left:0;top:4425px;width:1200px;text-align:center;font-size:14px}
</style>
</head>
<body>

<header class="abs site-header">
  <div class="abs brand" style="left:112px;top:38px"><span class="brand__dot"></span>Bright Meadow Skills</div>
  <div class="abs login"><span class="login__icon"></span>Log In</div>
  <div class="btn" style="left:862px;top:14px;width:227px;height:47px;font-size:14px">I need immediate service</div>
  <nav class="abs main-nav">
    <span class="is-active">Harbor Institute</span><span>Reviews</span><span>About</span><span>Upcoming Classes</span><span>Shop</span><span>Videos</span><span>Lost Certifiacate</span>
  </nav>
</header>

<section class="abs hero" role="img" aria-label="Video still: a woman in a cap firing a shotgun at an outdoor range with red targets">
  <div class="play" style="left:561px;top:288px;width:76px;height:76px"></div>
</section>
<div class="abs hero__quote display">“Your life may depend on what you learn in your concealed<br>carry training – don’t settle for a gun shop class!”</div>
<div class="btn btn--dark" style="left:392px;top:621px;width:201px;height:49px">Harbor Institute</div>
<div class="btn" style="left:607px;top:621px;width:201px;height:49px">Get tickets now</div>
<svg class="abs" style="left:0;top:670px" width="1200" height="140" viewBox="0 670 1200 140">
  <polygon points="0,680 600,795 1200,680 1200,690 600,805 0,690" fill="#e3162b"/>
</svg>
<div class="abs scroll-cue"></div>

<section>
  <div class="abs instructor-photo" role="img" aria-label="Black and white portrait of instructor Dennis Pollock"></div>
  <div class="abs eyebrow">About the instructor</div>
  <h1 class="abs instructor-name display">Dennis Pollock</h1>
  <p class="abs about-copy">Dennis Pollock is a 3rd generation Jacksonville native and delighted to be a part of this great community. He is a true security expert with 25 years of experience in the security industry. He has appeared on Channel 4, Metro 7, Coast 12 &amp; Bay 9 news outlets. He has been Featured in numerous publications and has trained thousands to protect themselves and their homes from thugs and thieves. He is certified by both the NSFA &amp; the NWDPA as a firearms instructor.</p>
  <div class="btn" style="left:642px;top:1196px;width:154px;height:49px;font-size:15px">Learn more</div>
</section>

<div class="abs levels-bg" role="img" aria-label="Dark background of scattered bullet cartridges"></div>
<svg class="abs" style="left:0;top:1320px" width="1200" height="110" viewBox="0 1320 1200 110">
  <polyline points="0,1330 600,1418 1200,1330" fill="none" stroke="#e3162b" stroke-width="5"/>
</svg>
<section>
  <h2 class="abs levels-title display">Our <span class="red">7 levels</span> of training take you from <span class="red">zero</span> to hero</h2>
  <p class="abs levels-copy">Wanna hear something funny? Guess what the average person asks about a concealed weapons class? “How much is it and how long is it?” Can you believe it? We are talking about preparing you for life and death situations and the main concern is “How Fast” and “How Cheap?” WOW! Why do most people settle for a cheap &amp; quick concealed carry class? It’s a fair question! Could you imagine a military soldier trained by a 2-hour class? How effective would they be in the heat of battle? If you want to be ready to SURVIVE an attack, YOU NEED MORE than a basic, run of the mill class! That’s why we created a PROPRIETARY 7 LEVEL TRAINING SYSTEM to take you all the way to the peak of readiness!</p>
  <div class="level" style="left:111px;top:1720px"><span class="level__num">1</span><span class="level__name">Concealed Carry<br>Class</span></div>
  <div class="level" style="left:359px;top:1720px"><span class="level__num">02</span><span class="level__name">Dynamic Defensive<br>Shooting</span></div>
  <div class="level" style="left:607px;top:1720px"><span class="level__num">03</span><span class="level__name">Fine Tuning Your<br>Technique</span></div>
  <div class="level" style="left:855px;top:1720px"><span class="level__num">04</span><span class="level__name">Virtual Threat-<br>Lab</span></div>
  <div class="level" style="left:236px;top:1900px"><span class="level__num">05</span><span class="level__name">Tactical Skills &amp;<br>Drills</span></div>
  <div class="level" style="left:484px;top:1900px"><span class="level__num">06</span><span class="level__name">Close Quarters<br>defense</span></div>
  <div class="level" style="left:732px;top:1900px"><span class="level__num">07</span><span class="level__name">Live Scenario<br>Threat-Lab</span></div>

  <svg class="abs" style="left:0;top:2240px" width="1200" height="40" viewBox="0 2240 1200 40">
    <line x1="0" y1="2272" x2="146" y2="2255" stroke="#e3162b" stroke-width="2"/>
    <line x1="1054" y1="2255" x2="1200" y2="2272" stroke="#e3162b" stroke-width="2"/>
  </svg>
  <div class="abs promo-video" role="img" aria-label="Video still: students practising drawing drills in a red-floored indoor training room">
    <div class="play" style="left:418px;top:185px;width:76px;height:76px"></div>
  </div>
  <div class="btn" style="left:465px;top:2637px;width:268px;height:51px;font-size:15px">Click here to learn more</div>
</section>

<div class="abs stories-bg" role="img" aria-label="Dark blurred background of a shooting range"></div>
<svg class="abs" style="left:0;top:2695px" width="1200" height="110" viewBox="0 2695 1200 110">
  <polyline points="0,2706 600,2792 1200,2706" fill="none" stroke="#e3162b" stroke-width="5"/>
</svg>
<section>
  <h2 class="abs stories-title display">Success stories</h2>
  <article class="story" style="left:111px">
    <div class="story__avatar" role="img" aria-label="Customer photo"></div>
    <div class="story__who"><span class="story__mark">“</span>- Marla K.</div>
    <p class="story__text">“I had never held a gun when I took the Bright Meadow Skills class and I’m hooked! I’m going all the way to level 7! Thank you Bright Meadow Skills!”</p>
    <div class="story__stars">★★★★★</div>
  </article>
  <article class="story" style="left:446px">
    <div class="story__avatar" role="img" aria-label="Customer photo"></div>
    <div class="story__who"><span class="story__mark">“</span>- Denise R.</div>
    <p class="story__text">“I was mugged here in Jacksonville and lived in fear ever since. It stole my happiness and I became scared to go out. I’m a Level 4 student and I feel sorry for the next thug that tries me!”</p>
    <div class="story__stars">★★★★★</div>
  </article>
  <article class="story" style="left:779px">
    <div class="story__avatar" role="img" aria-label="Customer photo"></div>
    <div class="story__who"><span class="story__mark">“</span>- Walt H</div>
    <p class="story__text">“I’ve been shooting for years and already had my concealed weapons license. My first class was a gun shop class and a waste of money. Dennis took the time to show me how to properly grip my gun and my shooting dramatically improved!”</p>
    <div class="story__stars">★★★★★</div>
  </article>
  <div class="abs dots"><i></i><i></i><i class="on"></i><i></i><i></i></div>
</section>

<div class="abs contact-bg"></div>
<svg class="abs" style="left:0;top:3395px" width="1200" height="100" viewBox="0 3395 1200 100">
  <polyline points="0,3490 600,3405 1200,3490" fill="none" stroke="#e3162b" stroke-width="5"/>
</svg>
<section>
  <h2 class="abs contact-title display">Get in touch</h2>
  <div class="field" style="left:248px;top:3558px;width:347px;height:49px">&#9679; First Name</div>
  <div class="field" style="left:603px;top:3558px;width:333px;height:49px">&#9679; Last Name</div>
  <div class="field" style="left:248px;top:3619px;width:688px;height:48px">&#9742; Your phone</div>
  <div class="field" style="left:248px;top:3678px;width:688px;height:50px">&#9993; Your Email</div>
  <div class="field field--area" style="left:248px;top:3738px;width:688px;height:129px">&#9998; How Can we help you?</div>
  <div class="btn" style="left:440px;top:3879px;width:307px;height:49px;font-size:15px">Submit
    <svg width="18" height="16" viewBox="0 0 18 16" style="margin-left:10px"><polygon points="0,7 18,0 13,16 9,10" fill="#fff"/></svg>
  </div>
</section>

<footer>
  <svg class="abs" style="left:0;top:4030px" width="1200" height="438" viewBox="0 4030 1200 438">
    <polygon points="0,4158 600,4036 1200,4158 1200,4468 0,4468" fill="#e3162b"/>
    <polygon points="0,4170 600,4048 1200,4170 1200,4468 0,4468" fill="#050505"/>
  </svg>
  <div class="abs brand" style="left:0;top:4190px;width:1200px;flex-direction:column;gap:14px;font-size:22px">
    <span class="brand__dot" style="width:44px;height:44px"></span>Bright Meadow Skills
  </div>
  <nav class="abs footer-nav"><span>Home</span><span>Harbor Institute</span><span>Reviews</span><span>About</span><span>Upcoming Classes</span><span>Shop</span><span>Videos</span><span>Lost Certifiacate</span></nav>
  <span class="social" style="left:527px"></span>
  <span class="social" style="left:565px"></span>
  <span class="social" style="left:601px"></span>
  <span class="social" style="left:639px"></span>
  <p class="abs copyright">Copyright Bright Meadow Skills 2021- All Rights Reserved</p>
</footer>

</body>
</html>
```